Business Card for a New Zealand IT Startup

I need a business card for VELTA Holdings. We are a young startup based in New Zealand working in internet marketing and web development. The design should have some element connected to New Zealand, such as wave, koru or silver fern, just don't use a kiwi bird.

```html
<!DOCTYPE html>
<html lang="en">
<head>
<meta charset="utf-8">
<title>VELTA Holdings – Business Card</title>
<link href="https://fonts.googleapis.com/css2?family=Open+Sans:wght@400;600;700&display=swap" rel="stylesheet">
<style>
  :root{
    --bg:#e4e4e4;
    --card:#fbfbfb;
    --blue:#1271b8;
    --orange:#e4561f;
    --ink:#2b2b2b;
    --white:#ffffff;
  }
  *{box-sizing:border-box;margin:0;padding:0}
  html,body{width:1200px;height:852px;overflow:hidden}
  body{background:var(--bg);font-family:"Open Sans",Arial,sans-serif;position:relative}
  .card{position:absolute;top:278px;width:520px;height:297px;border-radius:22px;background:var(--card);
        box-shadow:0 6px 14px rgba(0,0,0,.18);overflow:hidden}
  .card--front{left:60px}
  .card--back{left:620px}

  /* front */
  .brand{position:absolute;left:0;right:0;top:104px;display:flex;align-items:center;justify-content:center;gap:14px}
  .brand__dot{width:24px;height:24px;border-radius:50%;background:var(--blue)}
  .brand__name{font-weight:700;font-size:38px;letter-spacing:1px;color:var(--blue);line-height:1}
  .web-line{position:absolute;left:0;right:0;top:222px;display:flex;align-items:center;justify-content:center;gap:12px;
            font-size:13px;font-weight:600;color:var(--ink)}
  .web-line__rule{width:70px;height:2px;background:var(--blue)}

  /* back */
  .back-wave{position:absolute;inset:0}
  .side-brand{position:absolute;left:84px;top:148px;transform:translate(-50%,-50%) rotate(-90deg);
              display:flex;align-items:center;gap:10px;white-space:nowrap}
  .side-brand__dot{width:18px;height:18px;border-radius:50%;background:var(--blue)}
  .side-brand__name{font-weight:700;font-size:26px;color:var(--blue);letter-spacing:.5px;line-height:1}
  .contact{position:absolute;left:275px;top:68px;color:var(--white)}
  .contact__name{font-weight:700;font-size:19px;line-height:1.1}
  .contact__title{font-size:11px;margin-top:3px}
  .contact__address{font-size:12px;line-height:1.35;margin-top:22px}
  .contact__list{list-style:none;margin-top:8px;font-size:12px;line-height:1.6}
  .contact__list li{display:flex;align-items:center;gap:10px}
  .contact__list svg{width:11px;height:11px;fill:var(--white)}
</style>
</head>
<body>
  <section class="card card--front" aria-label="Business card front">
    <div class="brand">
      <span class="brand__dot"></span>
      <span class="brand__name">VELTA Holdings</span>
    </div>
    <div class="web-line">
      <span class="web-line__rule"></span>
      <span>www.veltaholdings.com</span>
      <span class="web-line__rule"></span>
    </div>
  </section>

  <section class="card card--back" aria-label="Business card back">
    <svg class="back-wave" viewBox="0 0 520 297" width="520" height="297" role="img" aria-label="Ocean wave band in orange to blue">
      <defs>
        <linearGradient id="wave-fill" x1="0.25" y1="1" x2="0.85" y2="0">
          <stop offset="0" stop-color="#e4561f"/>
          <stop offset="0.5" stop-color="#7a5c6e"/>
          <stop offset="1" stop-color="#1271b8"/>
        </linearGradient>
      </defs>
      <path d="M178 0 C128 60 214 130 176 200 C152 244 196 282 226 297"
            transform="translate(-9 0)" fill="none" stroke="#1271b8" stroke-width="7"/>
      <path d="M178 0 C128 60 214 130 176 200 C152 244 196 282 226 297 L520 297 L520 0 Z" fill="url(#wave-fill)"/>
    </svg>

    <div class="side-brand">
      <span class="side-brand__dot"></span>
      <span class="side-brand__name">VELTA Holdings</span>
    </div>

    <div class="contact">
      <p class="contact__name">Liam Carter Reid</p>
      <p class="contact__title">Managing Director</p>
      <p class="contact__address">18 Harbour Lane, Kelston,<br>Auckland, NZ 0602</p>
      <ul class="contact__list">
        <li><svg viewBox="0 0 24 24"><path d="M6.6 10.8a15 15 0 0 0 6.6 6.6l2.2-2.2a1 1 0 0 1 1-.25 11.4 11.4 0 0 0 3.6.57 1 1 0 0 1 1 1V20a1 1 0 0 1-1 1A17 17 0 0 1 3 4a1 1 0 0 1 1-1h3.5a1 1 0 0 1 1 1c0 1.25.2 2.45.57 3.57a1 1 0 0 1-.25 1z"/></svg>888-5555-321</li>
        <li><svg viewBox="0 0 24 24"><path d="M2 5h20v14H2z M3.5 6.5 12 13l8.5-6.5" fill="none" stroke="#fff" stroke-width="2"/></svg>hello@veltaholdings.com</li>
        <li><svg viewBox="0 0 24 24"><circle cx="12" cy="12" r="9.5" fill="none" stroke="#fff" stroke-width="2"/><path d="M2.5 12h19M12 2.5c-5 5-5 14 0 19M12 2.5c5 5 5 14 0 19" fill="none" stroke="#fff" stroke-width="1.6"/></svg>www.veltaholdings.com</li>
      </ul>
    </div>
  </section>
</body>
</html>
```